Photography business - business card design quick turn around

Create a business card design for me please. I actually need the final design back before the end of Sunday 13th May 7pm GMT. Sorry for the short notice.

Photoshop artwork template uploaded with artwork guidelines including printer profiles and other mandatory specifications. Only one side of the business card is required as the other side will be an image.

The design is required as an unflattened PSD file so that I can edit the text if I need to.

My brand colours are white and the teal you see in the logo. Occasionally I also use a dark grey on my website (I don't mind the shade of grey as appreciate grey on teal would be a different grey, to the grey I use on white on the website, so just use a shade of grey that matches). Font can be as the font for the logo or if you prefer I am open to another sans serif, easily legible font. Ideally font size will be 12+.Please do not use capital letters for text. I prefer everything to be lower case, if possible.

Thank you.

Lena

Target Market(s)

Other business owners who may refer me and families

Industry/Entity Type

Photographer

Contact Information for Business Card

Silver Kettle Photography Logo
Sub text: family portraits, held close with care

Contact information, ideally using simple icons to represent email / website / facebook / instagram / pinterest

email: lena@silverkettlephotography.co.uk
website: silverkettlephotography.co.uk
facebook: @silverkettlephotography
pinterest: pinmarks.net/silverkettlepho
instagram: @silverkettle_photography
mobile/telephone: 07713460291

If there is too much text then please drop the instagram and pinterest information.

Font styles to use
Sans Serif

Colors
33b8a4

Requirements
Must have
• Logo
• Contact details as listed above
• sub text
Nice to have
• Instagram and Pinterest contact details
• Nice to have icons to represent website / phone / facebook etc followered by the handle where relevant

```html
<!DOCTYPE html>
<html lang="en">
<head>
<meta charset="utf-8">
<title>Silver Kettle Photography – business cards</title>
<link rel="stylesheet" href="https://fonts.googleapis.com/css2?family=Montserrat:wght@400;500;600&display=swap">
<style>
  :root {
    --backdrop: #2a2c2e;
    --card: #1e2326;
    --teal: #33b8a4;
    --white: #ffffff;
    --silver: #c9ccce;
    --band-text: #14302b;
  }
  * { margin: 0; padding: 0; box-sizing: border-box; }
  html, body { width: 1200px; height: 880px; overflow: hidden; }
  body {
    background: var(--backdrop);
    font-family: "Montserrat", sans-serif;
    display: flex;
    align-items: center;
    justify-content: center;
    gap: 40px;
  }
  .card {
    position: relative;
    width: 540px;
    height: 310px;
    background: var(--card);
    overflow: hidden;
    border-radius: 3px;
  }
  .card-band {
    position: absolute;
    left: 0; right: 0; bottom: 0;
    height: 56px;
    background: var(--teal);
    border-top: 5px solid var(--white);
    box-shadow: 0 -6px 0 var(--card);
    display: flex;
    align-items: center;
    padding: 0 34px;
    color: var(--band-text);
    font-size: 14px;
    font-weight: 500;
    letter-spacing: 0.3px;
  }
  .card-front .card-band { justify-content: center; }

  .brand-mark {
    display: flex;
    align-items: center;
    gap: 12px;
    font-weight: 500;
    text-transform: uppercase;
    white-space: nowrap;
  }
  .brand-dot {
    border-radius: 50%;
    flex-shrink: 0;
  }
  .card-front .brand-mark {
    position: absolute;
    top: 104px;
    left: 0; right: 0;
    justify-content: center;
    color: var(--silver);
    font-size: 22px;
    letter-spacing: 1px;
  }
  .card-front .brand-dot { width: 26px; height: 26px; background: var(--silver); }

  .card-back .brand-mark {
    position: absolute;
    top: 34px; left: 34px;
    color: var(--teal);
    font-size: 22px;
    letter-spacing: 0.5px;
  }
  .card-back .brand-dot { width: 30px; height: 30px; background: var(--teal); }
  .tagline {
    position: absolute;
    top: 76px; left: 34px;
    color: var(--white);
    font-size: 13px;
    letter-spacing: 0.3px;
  }
  .person {
    position: absolute;
    top: 112px; left: 34px;
  }
  .person-name {
    color: var(--teal);
    font-size: 15px;
    font-weight: 600;
    text-transform: uppercase;
  }
  .person-role { color: var(--white); font-size: 11.5px; }
  .contact-list {
    position: absolute;
    top: 154px; left: 34px;
    list-style: none;
    display: flex;
    flex-direction: column;
    gap: 3px;
  }
  .contact-item {
    display: flex;
    align-items: center;
    gap: 8px;
    color: var(--white);
    font-size: 11.5px;
    white-space: nowrap;
  }
  .contact-icon { width: 15px; height: 15px; flex-shrink: 0; }
</style>
</head>
<body>

  <section class="card card-front" aria-label="card front">
    <div class="brand-mark"><span class="brand-dot"></span>Silver Kettle Photography</div>
    <div class="card-band">family portraits, held close with care</div>
  </section>

  <section class="card card-back" aria-label="card back">
    <div class="brand-mark"><span class="brand-dot"></span>Silver Kettle Photography</div>
    <p class="tagline">family portraits, held close with care</p>

    <div class="person">
      <p class="person-name">Mara Quill</p>
      <p class="person-role">Manager</p>
    </div>

    <ul class="contact-list">
      <li class="contact-item">
        <svg class="contact-icon" viewBox="0 0 16 16"><circle cx="8" cy="8" r="7" fill="none" stroke="#33b8a4" stroke-width="1.2"/><rect x="5.5" y="3.8" width="5" height="8.4" rx="1" fill="none" stroke="#33b8a4" stroke-width="1.1"/></svg>
        07713460291
      </li>
      <li class="contact-item">
        <svg class="contact-icon" viewBox="0 0 16 16"><circle cx="8" cy="8" r="7" fill="none" stroke="#33b8a4" stroke-width="1.2"/><rect x="4" y="5.2" width="8" height="5.6" fill="none" stroke="#33b8a4" stroke-width="1.1"/><path d="M4 5.4 8 8.6 12 5.4" fill="none" stroke="#33b8a4" stroke-width="1.1"/></svg>
        lena@silverkettlephotography.co.uk
      </li>
      <li class="contact-item">
        <svg class="contact-icon" viewBox="0 0 16 16"><circle cx="8" cy="8" r="7" fill="none" stroke="#33b8a4" stroke-width="1.2"/></svg>
        @silverkettlephotography
      </li>
      <li class="contact-item">
        <svg class="contact-icon" viewBox="0 0 16 16"><circle cx="8" cy="8" r="7" fill="none" stroke="#33b8a4" stroke-width="1.2"/></svg>
        pinmarks.net/silverkettlepho
      </li>
      <li class="contact-item">
        <svg class="contact-icon" viewBox="0 0 16 16"><circle cx="8" cy="8" r="7" fill="none" stroke="#33b8a4" stroke-width="1.2"/></svg>
        @silverkettle_photography
      </li>
    </ul>

    <div class="card-band">silverkettlephotography.co.uk</div>
  </section>

</body>
</html>
```